Fernhale Business Card Design

We are looking for a fresh business card design for our new logo. We would like a business card that is unique but friendly. We are in the window coverings business offering blinds, shutters and shades for homes.

Target Market(s)

Targeting the end-consumer

Industry/Entity Type

Business

Requirements
Must have
• Must have a dedicates space for a photo of our sales person. Must contain our new logo (attached).

```html
<!DOCTYPE html>
<html lang="en">
<head>
<meta charset="utf-8">
<title>Fernhale Business Card</title>
<link href="https://fonts.googleapis.com/css2?family=Lato:wght@400;700&family=Montserrat:wght@400;600&display=swap" rel="stylesheet">
<style>
  :root {
    --green: #7dc242;
    --slate: #5b5c60;
    --ink: #4d4e52;
    --card: #f7f7f7;
    --card-edge: #ececec;
    --backdrop: #2b2b2d;
    --photo-top: #e4e6e3;
    --photo-bottom: #c9ccc8;
  }
  * { margin: 0; padding: 0; box-sizing: border-box; }
  html, body { width: 1200px; height: 791px; overflow: hidden; background: var(--backdrop); }
  .stage { position: relative; width: 1200px; height: 791px; }
  .card {
    position: absolute; left: 310px; width: 580px; height: 320px;
    background: linear-gradient(160deg, #ffffff 0%, var(--card) 60%, var(--card-edge) 100%);
    overflow: hidden; font-family: "Lato", sans-serif; color: var(--ink);
  }
  .card--front { top: 60px; }
  .card--back { top: 411px; }

  .tab { position: absolute; display: flex; height: 46px; }
  .tab__green { width: 26px; background: var(--green); }
  .tab__slate { width: 7px; background: var(--slate); }
  .tab--left { left: 0; }
  .tab--left .tab__slate { margin-left: 4px; }
  .tab--right { right: 0; flex-direction: row-reverse; }
  .tab--right .tab__slate { margin-right: 4px; }

  .rule { position: absolute; height: 2px; background: var(--green); }

  .brand { position: absolute; display: flex; align-items: center; gap: 10px; }
  .brand__mark { width: 30px; height: 30px; border: 2px solid var(--slate); border-radius: 4px; }
  .brand__name { font-size: 30px; font-weight: 400; color: var(--slate); letter-spacing: 0.5px; line-height: 1; }

  /* front */
  .card--front .tab { top: 150px; }
  .card--front .brand { left: 52px; top: 158px; }
  .card--front .rule { left: 0; right: 0; top: 194px; }
  .website { position: absolute; right: 26px; top: 164px; display: flex; align-items: center; gap: 8px; font-size: 15px; letter-spacing: 0.4px; }

  /* back */
  .card--back .tab--right { top: 44px; }
  .card--back .rule--top { left: 0; right: 0; top: 88px; }
  .person { position: absolute; right: 50px; top: 46px; text-align: right; font-family: "Montserrat", sans-serif; }
  .person__name { font-size: 19px; font-weight: 600; letter-spacing: 0.5px; color: var(--slate); line-height: 1.2; }
  .person__name .first { color: var(--green); }
  .person__role { font-size: 12px; letter-spacing: 0.5px; color: var(--ink); }
  .card--back .tab--left { top: 128px; }
  .card--back .brand { left: 52px; top: 136px; }
  .card--back .rule--bottom { left: 0; right: 0; top: 174px; }

  .contacts { position: absolute; left: 60px; top: 192px; list-style: none; }
  .contacts li { display: flex; align-items: center; gap: 16px; height: 27px; font-size: 14px; letter-spacing: 0.3px; }
  .contacts svg { width: 18px; height: 18px; flex: none; }

  .sales-photo {
    position: absolute; right: 50px; top: 190px; width: 96px; height: 112px;
    background: linear-gradient(180deg, var(--photo-top), var(--photo-bottom));
    border: 3px solid #ffffff; box-shadow: 0 0 0 1px var(--green);
  }
</style>
</head>
<body>
<div class="stage">

  <section class="card card--front" aria-label="Card front">
    <div class="tab tab--left"><span class="tab__green"></span><span class="tab__slate"></span></div>
    <div class="brand"><span class="brand__mark"></span><span class="brand__name">Fernhale</span></div>
    <div class="website">www.fernhalehome.com
      <svg width="13" height="13" viewBox="0 0 14 14" fill="none" stroke="#5b5c60" stroke-width="1.2"><circle cx="7" cy="7" r="6"/><ellipse cx="7" cy="7" rx="2.6" ry="6"/><line x1="1" y1="7" x2="13" y2="7"/></svg>
    </div>
    <div class="rule"></div>
  </section>

  <section class="card card--back" aria-label="Card back">
    <div class="tab tab--right"><span class="tab__green"></span><span class="tab__slate"></span></div>
    <div class="person">
      <div class="person__name"><span class="first">DANA</span> WHITLOW</div>
      <div class="person__role">GRAPHIC DESIGNER</div>
    </div>
    <div class="rule rule--top"></div>

    <div class="tab tab--left"><span class="tab__green"></span><span class="tab__slate"></span></div>
    <div class="brand"><span class="brand__mark"></span><span class="brand__name">Fernhale</span></div>
    <div class="rule rule--bottom"></div>

    <ul class="contacts">
      <li>
        <svg viewBox="0 0 18 18"><rect x="1" y="4" width="16" height="10" fill="#7dc242"/><polyline points="1,4 9,10 17,4" fill="none" stroke="#fff" stroke-width="1.3"/></svg>
        dana@brightmoorhome.com
      </li>
      <li>
        <svg viewBox="0 0 18 18"><rect x="5" y="1" width="9" height="16" rx="1.5" fill="none" stroke="#7dc242" stroke-width="1.6"/><circle cx="9.5" cy="14" r="1" fill="#7dc242"/></svg>
        (office) - (1) 555 0142 318
      </li>
      <li>
        <svg viewBox="0 0 18 18"><circle cx="9" cy="9" r="8" fill="#7dc242"/><ellipse cx="9" cy="9" rx="3.4" ry="8" fill="none" stroke="#fff" stroke-width="1.1"/><line x1="1" y1="9" x2="17" y2="9" stroke="#fff" stroke-width="1.1"/></svg>
        www.brightmoorhome.com
      </li>
      <li>
        <svg viewBox="0 0 18 18"><path d="M9 1a5.5 5.5 0 0 0-5.5 5.5C3.5 11 9 17 9 17s5.5-6 5.5-10.5A5.5 5.5 0 0 0 9 1z" fill="#5b5c60"/><circle cx="9" cy="6.5" r="2" fill="#fff"/></svg>
        27, 2nd Floor, Elm Court, NY 100482
      </li>
    </ul>

    <div class="sales-photo" role="img" aria-label="Photo of the salesperson"></div>
  </section>

</div>
</body>
</html>
```